Fun relaxed Travel Photography Business Card*

Require a fun, funky and quirky but rememberable business card for a travel photographer

Industry/Entity Type

Photographer

Contact Information for Business Card

Front Card

(my name) Lenn D.

Travel Photographer ( small under travel photographer) “self-proclaimed”

(website logo) wanderingsoflenn.net

(Instagram logo) @wanderings_of_lenn

(Instagram logo) @wanderings_of_lenn_2.0 (backup for when Instagram puts Lenn on timeout for bad behaviour)

Tel: N/A (removing the potential awkwardness of me not replying)

Email: (see above)

Back Card

Offending people since 1986

(Bottom right corner) “p.s. travelling made me fatTER”

Font styles to use
Serif

Colors

Designer to choose colors to be used in the design.

Requirements
Must have
• a camera
• a similar cartoon version of me as the "logo" see attached files, try to make as similar as possible

```html
<!DOCTYPE html>
<html lang="en">
<head>
<meta charset="utf-8">
<title>Lenn D. — Travel Photographer Business Card</title>
<link rel="stylesheet" href="https://fonts.googleapis.com/css2?family=Montserrat:wght@400;500;700&family=Righteous&display=swap">
<style>
  :root {
    --backdrop: #1b1d21;
    --card: #101011;
    --card-edge: #1d1d1f;
    --silver: #e6e6e6;
    --silver-soft: #bdbdbd;
    --silver-dim: #8a8a8a;
  }
  * { box-sizing: border-box; margin: 0; padding: 0; }
  html, body {
    width: 1200px; height: 900px; overflow: hidden;
    background: var(--backdrop);
    font-family: "Montserrat", sans-serif;
  }
  .canvas {
    width: 1200px; height: 900px;
    display: flex; align-items: center; justify-content: center; gap: 40px;
  }
  .card {
    position: relative;
    width: 540px; height: 310px;
    background: var(--card);
    border-radius: 26px;
    box-shadow: 0 6px 0 var(--card-edge), 0 18px 40px rgba(0,0,0,.55);
    color: var(--silver);
  }
  /* Front */
  .logo-mark {
    position: absolute; left: 50px; top: 40px;
    width: 190px; height: 160px;
    border-radius: 50% 46% 50% 48%;
    background: radial-gradient(circle at 55% 60%, #cfcfcf 0%, #6d6d6d 40%, #1a1a1a 75%);
    opacity: .55;
  }
  .identity {
    position: absolute; right: 38px; bottom: 30px;
    text-align: right;
  }
  .identity__name {
    font-weight: 700; font-size: 24px; letter-spacing: .5px;
    text-transform: uppercase; line-height: 1.05;
  }
  .identity__title {
    font-weight: 700; font-size: 13px; letter-spacing: .4px;
    text-transform: uppercase;
  }
  .identity__note {
    font-size: 10px; text-transform: uppercase; color: var(--silver-soft);
    margin-bottom: 14px;
  }
  .contact { list-style: none; }
  .contact__item {
    display: flex; justify-content: flex-end; align-items: center; gap: 10px;
    font-size: 14px; line-height: 1.45; color: var(--silver);
  }
  .contact__icon { width: 16px; height: 16px; flex: none; }
  .contact__square {
    width: 14px; height: 14px; flex: none; margin: 1px;
    border: 1.6px solid var(--silver); border-radius: 3px;
  }
  /* Back */
  .slogan {
    position: absolute; left: 0; right: 0; top: 112px;
    text-align: center;
    font-family: "Righteous", sans-serif;
    font-size: 27px; letter-spacing: 1px; text-transform: uppercase;
    color: var(--silver);
  }
  .postscript {
    position: absolute; right: 34px; bottom: 30px;
    font-size: 13px; color: var(--silver-soft);
  }
  .postscript strong { font-weight: 700; color: var(--silver); }
</style>
</head>
<body>
<main class="canvas">
  <section class="card card--front">
    <div class="logo-mark" role="img" aria-label="Silver line logo: a camera lens with a bird perched on top"></div>
    <div class="identity">
      <h1 class="identity__name">Lenn D.</h1>
      <p class="identity__title">Travel Photographer</p>
      <p class="identity__note">(Self-proclaimed)</p>
      <ul class="contact">
        <li class="contact__item">wanderingsoflenn.net
          <svg class="contact__icon" viewBox="0 0 16 16" fill="none" stroke="currentColor" stroke-width="1.3">
            <circle cx="8" cy="8" r="6.8"/><ellipse cx="8" cy="8" rx="3" ry="6.8"/>
            <line x1="1.2" y1="8" x2="14.8" y2="8"/><line x1="2.3" y1="4.5" x2="13.7" y2="4.5"/><line x1="2.3" y1="11.5" x2="13.7" y2="11.5"/>
          </svg>
        </li>
        <li class="contact__item">@wanderings_of_lenn <span class="contact__square"></span></li>
        <li class="contact__item">@wanderings_of_lenn_2.0 <span class="contact__square"></span></li>
        <li class="contact__item">N/A
          <svg class="contact__icon" viewBox="0 0 16 16" fill="currentColor">
            <path d="M4.2 1.5l2 3.2-1.3 1.4c.8 1.8 2.2 3.3 4 4.2l1.4-1.3 3.2 2-1 2.6C7.6 13.5 2.4 8.4 1.6 2.6z"/>
          </svg>
        </li>
        <li class="contact__item">N/A
          <svg class="contact__icon" viewBox="0 0 16 16" fill="none" stroke="currentColor" stroke-width="1.4">
            <rect x="1" y="3.5" width="14" height="9.5" rx="1"/><polyline points="1,3.8 8,9 15,3.8"/>
          </svg>
        </li>
      </ul>
    </div>
  </section>

  <section class="card card--back">
    <p class="slogan">Offending people since 1986</p>
    <p class="postscript">p.s. travelling made me fat<strong>TER</strong></p>
  </section>
</main>
</body>
</html>
```